Construction material supplies company business card ****

1. Full company name “K T Masonry Works Ltd”
I am after a Business card design for the company as a whole. We are better known in Solomon Islands as “K T Masonry” for short.

We are a building materials supplier of
Ready Mixed Concrete, Bricks and Blocks,
Quarry products- gravel, aggregates, sand etc.
Cement distributor/retailer of reputable brands.
Other prefab concrete products. Culverts, wave breakers, concrete retaining blocks etc.

2. Competitive Advantage over Competition: Quality, efficient, professional, dependable, reliable

3. We want people to feel trust worthy, high quality, strong when they see our brand

5. No preference to color. Maybe more sturdy and corporate. Not fancy.

Industry/Entity Type

CONSTRUCTION SUPPLY

Contact Information for Business Card

Name, Position, office phone mob phone, email

Requirements
Must have
• the company logo
Nice to have
• would like to see a mixture of designs, of with logo only and also with simple graphic designs to bring out the company whilst still have the strong sturdy professional feeling

```html
<!DOCTYPE html>
<html lang="en">
<head>
<meta charset="utf-8">
<title>K T Masonry – Business Card</title>
<link rel="stylesheet" href="https://fonts.googleapis.com/css2?family=Arimo:wght@400;700&display=swap">
<style>
  :root {
    --navy: #16426b;
    --white: #ffffff;
    --ink: #333a40;
    --rule: #b9bec3;
    --stage: #202224;
  }
  * { box-sizing: border-box; margin: 0; padding: 0; }
  html, body {
    width: 1200px; height: 1015px; overflow: hidden;
    background: var(--stage);
    font-family: "Arimo", Arial, sans-serif;
  }
  .card {
    position: absolute; left: 250px;
    width: 700px; height: 400px;
    box-shadow: 0 10px 30px rgba(0,0,0,.5);
  }
  /* Front */
  .card--front { top: 60px; background: var(--navy); color: var(--white); }
  .front-brand {
    position: absolute; top: 120px; left: 0; right: 0;
    display: flex; justify-content: center; align-items: center; gap: 18px;
  }
  .brand-mark { width: 34px; height: 34px; background: currentColor; }
  .brand-name { font-weight: 700; font-size: 52px; letter-spacing: 3px; text-transform: uppercase; }
  .front-products {
    position: absolute; top: 228px; left: 118px; right: 60px;
    font-size: 17px; line-height: 1.35;
  }
  .front-products strong { font-weight: 700; text-transform: uppercase; }

  /* Back */
  .card--back { top: 520px; background: var(--white); color: var(--navy); }
  .back-brand {
    position: absolute; left: 40px; top: 70px; width: 330px;
    display: flex; flex-direction: column; align-items: center; gap: 18px;
  }
  .back-brand .brand-mark { width: 40px; height: 40px; }
  .back-brand .brand-name { font-size: 44px; }
  .divider {
    position: absolute; left: 390px; top: 40px; width: 1px; height: 190px;
    background: var(--rule);
  }
  .contact { position: absolute; left: 420px; top: 42px; color: var(--ink); }
  .contact-name { color: var(--navy); font-weight: 700; font-size: 25px; text-transform: uppercase; letter-spacing: .5px; }
  .contact-role { font-size: 16px; margin-bottom: 16px; }
  .contact-list { list-style: none; font-size: 16px; line-height: 1.55; }
  .contact-list li { display: flex; align-items: center; gap: 10px; }
  .contact-list svg { width: 16px; height: 16px; fill: var(--navy); flex: none; }
  .band {
    position: absolute; left: 0; right: 0; bottom: 0; height: 118px;
    background: var(--navy); color: var(--white);
    display: flex; flex-direction: column; justify-content: center; align-items: center;
    font-size: 16px; line-height: 1.35; text-transform: uppercase; letter-spacing: .3px;
  }
</style>
</head>
<body>

<section class="card card--front">
  <div class="front-brand">
    <span class="brand-mark" aria-hidden="true"></span>
    <span class="brand-name">K T Masonry</span>
  </div>
  <p class="front-products">
    <strong>Quarry products:</strong> Gravel, Aggregates, sand etc.<br>
    <strong>Concrete products:</strong> Culverts, Wave breakers<br>
    Concrete retaining blocks etc.
  </p>
</section>

<section class="card card--back">
  <div class="back-brand">
    <span class="brand-mark" aria-hidden="true"></span>
    <span class="brand-name">K T Masonry</span>
  </div>
  <div class="divider"></div>
  <div class="contact">
    <p class="contact-name">Daniel Roberts</p>
    <p class="contact-role">Managing Director</p>
    <ul class="contact-list">
      <li><svg viewBox="0 0 16 16" aria-hidden="true"><path d="M3.6 1.5l2.3 2.6-1.3 1.6c.9 1.9 2.2 3.3 4.1 4.3l1.6-1.3 2.6 2.3-1.3 2.3C7 13 3 9 1.4 2.8z"/></svg>044-987 654 321</li>
      <li><svg viewBox="0 0 16 16" aria-hidden="true"><path d="M4 1h8v14H4zM5.5 2.5v9h5v-9zM7.3 12.6h1.4v1.2H7.3z" fill-rule="evenodd"/></svg>044-987 654 321</li>
      <li><svg viewBox="0 0 16 16" aria-hidden="true"><path d="M1 3.5h14v9H1zM2 4.5l6 4.5 6-4.5v-.3H2z"/></svg>info@mailsample.com</li>
      <li><svg viewBox="0 0 16 16" aria-hidden="true"><path d="M8 1a7 7 0 100 14A7 7 0 008 1zm0 1.3c.8.8 1.4 2.2 1.6 3.9H6.4C6.6 4.5 7.2 3.1 8 2.3zM2.4 7.3h2.8c0 .5 0 1 .1 1.4H2.4a5.7 5.7 0 010-1.4zm4 0h3.2v1.4H6.4zm4.4 0h2.8a5.7 5.7 0 010 1.4h-2.8zM6.4 9.8h3.2c-.2 1.7-.8 3.1-1.6 3.9-.8-.8-1.4-2.2-1.6-3.9z"/></svg>www.sitesample.com</li>
    </ul>
  </div>
  <div class="band">
    <span>Ready mixed concrete, bricks and blocks</span>
    <span>Cement distributor/retailer of reputable brands</span>
  </div>
</section>

</body>
</html>
```